Local Flower Farm Needs Business Card Design

I need business cards designed for a flower farm based in Eudora, Kansas.
Business Info:
We are a local cut flower farm located in Eudora, Kansas, founded by Corinne Haldwick. What started as a passion for agriculture and search for more joy in daily life has blossomed into a small business dedicated to providing the community with beautiful, fresh, and sustainable flowers. We specialize in local, seasonal blooms, ensuring that every petal reflects the care and dedication we pour into our craft. Our mission is to deliver the highest quality flowers directly to our customers through local farmers markets and to florists who share our commitment to sustainability. Join us in celebrating the beauty of nature, one bloom at a time!
Contact Details:
Corinne Haldwick
Owner
Phone 913-555-0147
Facebook: Rosalind Thorpe Gardens
Instagram: @RosalindThorpeGardens
Website: RosalindThorpeGardens.example
Target Market(s)
Wholesale to Florists and Direct to Consumer via Farmers Market
Industry/Entity Type
Florist, Farm
Contact Information for Business Card
Name, Contact Info, Logo
Look and feel
Each slider illustrates characteristics of the customer's brand and the style your logo design should communicate.

```html
<!DOCTYPE html>
<html lang="en">
<head>
<meta charset="utf-8">
<title>Rosalind Thorpe Gardens – Business Card</title>
<link rel="stylesheet" href="https://fonts.googleapis.com/css2?family=Cormorant+Garamond:wght@500;600&family=Montserrat:wght@400;500&display=swap">
<style>
  :root {
    --teal: #0c2a30;
    --white: #ffffff;
    --stage: #2b2b2b;
    --sprig: #46626a;
    --serif: "Cormorant Garamond", Georgia, serif;
    --sans: "Montserrat", Arial, sans-serif;
  }
  * { box-sizing: border-box; margin: 0; padding: 0; }
  html, body { width: 1200px; height: 1015px; overflow: hidden; }
  body {
    background: var(--stage);
    display: flex; flex-direction: column; align-items: center; justify-content: center;
    gap: 50px;
  }
  .card {
    position: relative;
    width: 760px; height: 434px;
    overflow: hidden;
    box-shadow: 0 10px 30px rgba(0,0,0,.45);
  }
  .card--front { background: var(--teal); }
  .card--back { background: var(--white); }

  .brand-seal {
    position: absolute;
    width: 210px; height: 210px;
    border-radius: 50%;
    display: flex; align-items: center; justify-content: center;
    text-align: center;
    font-family: var(--serif); font-weight: 600;
    font-size: 27px; line-height: 1.15; letter-spacing: .06em;
    text-transform: uppercase;
  }
  .card--front .brand-seal { left: 275px; top: 70px; border: 1.5px solid var(--white); color: var(--white); }
  .card--back .brand-seal { left: 70px; top: 100px; border: 1.5px solid var(--teal); color: var(--teal); }

  .front-web {
    position: absolute; left: 0; right: 0; bottom: 58px;
    text-align: center; color: var(--white);
    font-family: var(--sans); font-weight: 500; font-size: 19px; letter-spacing: .03em;
  }

  .wave { position: absolute; inset: 0; }

  .holder {
    position: absolute; right: 48px; top: 34px; text-align: right; color: var(--teal);
  }
  .holder__name { font-family: var(--serif); font-weight: 600; font-size: 27px; letter-spacing: .05em; text-transform: uppercase; }
  .holder__role { font-family: var(--sans); font-size: 13px; margin-top: 2px; }

  .contact-list {
    position: absolute; right: 36px; top: 215px;
    list-style: none; color: var(--white);
    font-family: var(--sans); font-size: 17px; font-weight: 500;
  }
  .contact-list li {
    display: flex; align-items: center; justify-content: flex-end; gap: 10px;
    height: 34px;
  }
  .contact-icon {
    width: 24px; height: 24px; border: 1.5px solid var(--white); border-radius: 50%;
    display: flex; align-items: center; justify-content: center; flex: none;
  }
</style>
</head>
<body>

  <section class="card card--front" aria-label="Card front">
    <div class="brand-seal">Rosalind<br>Thorpe<br>Gardens</div>
    <p class="front-web">RosalindThorpeGardens.example</p>
  </section>

  <section class="card card--back" aria-label="Card back">
    <svg class="wave" width="760" height="434" viewBox="0 0 760 434" aria-hidden="true">
      <path d="M0,434 L0,392 C200,385 330,360 410,272 C480,185 560,138 760,100 L760,434 Z" fill="var(--teal)"/>
      <path d="M0,392 C200,385 330,360 410,272 C480,185 560,138 760,100" transform="translate(0,-12)" fill="none" stroke="var(--teal)" stroke-width="3"/>
    </svg>
    <svg class="wave" width="760" height="434" viewBox="0 0 760 434">
      <rect role="img" aria-label="Fine-line floral sprigs along the wave" x="245" y="322" width="100" height="12" rx="6" fill="var(--sprig)" opacity=".35" transform="rotate(-20 295 328)"/>
      <rect role="img" aria-label="Fine-line floral sprigs along the wave" x="585" y="106" width="110" height="12" rx="6" fill="var(--sprig)" opacity=".35" transform="rotate(-15 640 112)"/>
    </svg>

    <div class="brand-seal">Rosalind<br>Thorpe<br>Gardens</div>

    <div class="holder">
      <p class="holder__name">Corinne Haldwick</p>
      <p class="holder__role">Owner</p>
    </div>

    <ul class="contact-list">
      <li>913-555-0147
        <span class="contact-icon">
          <svg width="12" height="12" viewBox="0 0 24 24" aria-hidden="true"><path d="M6.6 10.8a15 15 0 0 0 6.6 6.6l2.2-2.2a1 1 0 0 1 1-.25 11 11 0 0 0 3.6.6 1 1 0 0 1 1 1V20a1 1 0 0 1-1 1A17 17 0 0 1 3 4a1 1 0 0 1 1-1h3.5a1 1 0 0 1 1 1 11 11 0 0 0 .6 3.6 1 1 0 0 1-.25 1z" fill="var(--white)"/></svg>
        </span>
      </li>
      <li>Rosalind Thorpe Gardens <span class="contact-icon"></span></li>
      <li>@RosalindThorpeGardens <span class="contact-icon"></span></li>
      <li>RosalindThorpeGardens.example
        <span class="contact-icon">
          <svg width="14" height="14" viewBox="0 0 24 24" aria-hidden="true" fill="none" stroke="var(--white)" stroke-width="2"><circle cx="12" cy="12" r="9"/><path d="M3 12h18M12 3c3 3 3 15 0 18M12 3c-3 3-3 15 0 18"/></svg>
        </span>
      </li>
    </ul>
  </section>

</body>
</html>
```